Website setup with Brightline (childtheme is velmora theme)

hey there, my name is tobias and i would need a website. Tundrix Framework, I use the velmora theme. I would like to say goodbye to the eye-catching website with a nice menu. I like to send you some example from websites I like. Https://harborquillnotes.com/about/ https://harborquillnotes.com The main tabs on the top should be "About", "Blog", "Video", "Resources" on the right / blog /

Number of Pages Required

1 page

Colors
0493ce
fbee3d
faa54b

```html
<!DOCTYPE html>
<html lang="en">
<head>
<meta charset="utf-8">
<title>Tobias Life — Life and Business Coach</title>
<link rel="stylesheet" href="https://fonts.googleapis.com/css2?family=Mulish:wght@400;600;700;800;900&display=swap">
<style>
:root{
  --red:#ee4a2f;
  --red-dark:#d63c22;
  --ink:#1c1c1c;
  --muted:#8a8a8a;
  --cream:#fbf8ec;
  --light:#f1f1f3;
  --night:#151a22;
  --black:#0b0b0b;
  --white:#ffffff;
  --fb:#34508c;
  --slate:#4f6d8c;
  --sky:#2e9fe0;
}
*{margin:0;padding:0;box-sizing:border-box}
html,body{width:1200px;height:4928px;overflow:hidden}
body{font-family:"Mulish",Arial,sans-serif;color:var(--ink);background:var(--white);position:relative}
.abs{position:absolute}
.photo{position:absolute}

/* header + hero */
.hero{position:absolute;left:0;top:0;width:1200px;height:640px;overflow:hidden}
.hero-photo{left:0;top:0;width:1200px;height:640px;background:linear-gradient(100deg,#3d3b3a 0%,#6c6966 35%,#a8a39c 55%,#d9d3c8 75%,#efeae0 100%)}
.hero-shade{left:0;top:0;width:1200px;height:640px;background:linear-gradient(90deg,rgba(20,20,20,.55),rgba(20,20,20,.1) 60%,rgba(20,20,20,0))}
.brand{left:98px;top:64px;color:var(--white);font-size:30px;font-weight:700}
.nav{left:458px;top:72px;display:flex;gap:38px;list-style:none}
.nav li{color:var(--white);font-size:15px;font-weight:700;letter-spacing:.5px;position:relative}
.nav li.active{color:var(--red)}
.nav li.active::after{content:"";position:absolute;left:0;right:0;top:28px;height:3px;background:var(--red)}
.search{left:1060px;top:62px;width:38px;height:38px;border-radius:50%;background:var(--red)}
.hero-title{left:98px;top:296px;color:var(--white);font-size:46px;font-weight:800;line-height:1.22;letter-spacing:.5px}

.newsletter{left:172px;top:500px;width:856px;height:268px;background:var(--red);box-shadow:0 10px 30px rgba(0,0,0,.18)}
.newsletter h3{position:absolute;left:0;right:0;top:40px;text-align:center;color:var(--white);font-size:30px;font-weight:700}
.form-row{position:absolute;left:72px;top:124px;width:712px;height:72px;background:rgba(255,255,255,.25);display:flex;gap:14px;padding:14px}
.field{flex:1;background:var(--white);font-size:14px;color:#888;padding:14px 16px}
.btn-sign{width:220px;background:var(--black);color:var(--white);font-size:15px;font-weight:700;text-align:center;padding-top:13px}
.newsletter p{position:absolute;left:0;right:0;top:214px;text-align:center;color:var(--white);font-size:14px;opacity:.9}

/* about */
.about{left:0;top:640px;width:1200px;height:840px;background:var(--cream)}
.about-photo{left:600px;top:0;width:600px;height:780px;background:linear-gradient(90deg,rgba(251,248,236,1) 0%,rgba(210,208,204,.7) 30%,#8f8d8b 70%,#6e6c6b 100%)}
.about-arrow{left:420px;top:90px}
.about h2{position:absolute;left:100px;top:260px;font-size:44px;font-weight:800;color:#444}
.about h4{position:absolute;left:100px;top:326px;font-size:28px;font-weight:600;color:var(--red)}
.about .copy{position:absolute;left:100px;width:500px;font-size:14px;line-height:1.75;color:#888}
.stats{position:absolute;left:100px;top:636px;display:flex;gap:4px}
.stat{width:120px;height:58px;display:flex;align-items:center;gap:10px;padding:0 14px;color:var(--white)}
.stat i{display:block;width:22px;height:22px;border-radius:3px;background:rgba(255,255,255,.85)}
.stat b{display:block;font-size:16px;font-weight:800}
.stat span{display:block;font-size:11px}

/* resources */
.section-title{position:absolute;left:0;width:1200px;text-align:center;font-size:40px;font-weight:700;color:#333}
.card-img{position:absolute;width:320px;height:230px}
.card-title{position:absolute;width:320px;text-align:center;font-size:21px;font-weight:600;color:#333}
.card-text{position:absolute;width:300px;text-align:center;font-size:13px;line-height:1.7;color:#999}
.btn{position:absolute;background:var(--red);color:var(--white);font-size:16px;font-weight:700;display:flex;align-items:center;justify-content:center;gap:10px}

/* video */
.video{left:0;top:2330px;width:1200px;height:540px;background:var(--light)}
.video-photo{left:0;top:0;width:680px;height:540px;background:linear-gradient(110deg,#2a3140 0%,#55617a 40%,#a3adbc 75%,rgba(241,241,243,1) 100%)}
.play{left:268px;top:224px}
.video h3{position:absolute;left:614px;top:92px;font-size:40px;font-weight:700;line-height:1.3;color:#333}
.video p{position:absolute;left:614px;top:228px;width:480px;font-size:14px;line-height:1.8;color:#999}

/* blog */
.post-title{position:absolute;font-size:15px;font-weight:800;color:#222;letter-spacing:.3px}
.post-text{position:absolute;width:310px;font-size:13px;line-height:1.7;color:#999}

/* reach */
.reach{left:0;top:3712px;width:1200px;height:490px;background:var(--night)}
.reach-bg{left:0;top:0;width:1200px;height:490px;background:linear-gradient(90deg,#1d232d 0%,#2b323c 55%,#3b3f46 100%)}
.reach-map{left:740px;top:126px;width:380px;height:226px;background:radial-gradient(ellipse at center,rgba(220,220,225,.35),rgba(220,220,225,.08) 70%,rgba(0,0,0,0))}
.reach h2{position:absolute;left:98px;top:116px;font-size:40px;font-weight:700;color:var(--white)}
.avatar{left:100px;top:256px;width:110px;height:110px;border-radius:50%;background:linear-gradient(160deg,#9aa3ad,#59626d);border:4px solid var(--white)}
.avatar-badge{left:176px;top:326px;width:36px;height:36px;border-radius:50%;background:var(--red)}
.quote{position:absolute;left:262px;top:256px;width:470px;font-size:14px;line-height:1.8;color:#ccc}
.quote-name{position:absolute;left:262px;top:394px;font-size:14px;color:#ddd}
.quote-name b{color:var(--red)}
.dots{left:262px;top:428px;display:flex;gap:8px}
.dots span{width:9px;height:9px;border-radius:50%;background:#777}
.dots span:first-child{background:var(--red)}

/* partners */
.partners{left:0;top:4202px;width:1200px;height:190px;background:var(--white);display:flex;align-items:center;justify-content:space-around;padding:0 100px}
.partner{font-size:30px;font-weight:800;color:#333}

/* footer */
.footer{left:0;top:4392px;width:1200px;height:536px;background:var(--black);border-top:6px solid var(--red);color:#ccc}
.footer h5{position:absolute;font-size:18px;font-weight:800;color:var(--white);letter-spacing:.5px}
.footer .about-text{position:absolute;left:100px;top:138px;width:380px;font-size:13px;line-height:1.8;color:#bbb}
.connect-rule{left:590px;top:78px;width:260px;height:1px;background:#444}
.socials{left:590px;top:150px;display:flex;gap:8px}
.socials span{width:30px;height:30px;border-radius:50%;background:var(--white)}
.foot-avatar{left:966px;top:88px;width:114px;height:114px;border-radius:50%;background:#d8d8d8}
.foot-name{position:absolute;left:966px;top:216px;width:114px;text-align:center;font-size:14px;color:var(--white)}
.foot-rule{left:100px;top:300px;width:1000px;height:1px;background:#333}
.foot-nav{left:0;top:384px;width:1200px;display:flex;justify-content:center;gap:34px;font-size:13px;font-weight:700;color:var(--white)}
.foot-legal{left:0;top:418px;width:1200px;display:flex;justify-content:center;gap:24px;font-size:11px;color:#aaa}
.copyright{left:0;top:450px;width:1200px;text-align:center;font-size:11px;color:#888}
</style>
</head>
<body>

<header class="hero">
  <div class="photo hero-photo" role="img" aria-label="Photo of a smiling business coach in a suit with colleagues behind him in a bright office"></div>
  <div class="photo hero-shade"></div>
  <div class="abs brand">Tobias Life</div>
  <ul class="abs nav">
    <li class="active">HOME</li><li>ABOUT</li><li>BLOG</li><li>VIDEO</li><li>RESOURCES</li><li>CONTACT</li>
  </ul>
  <div class="abs search">
    <svg width="38" height="38" viewBox="0 0 38 38"><circle cx="17" cy="17" r="6" fill="none" stroke="#fff" stroke-width="2.5"/><line x1="21.5" y1="21.5" x2="26" y2="26" stroke="#fff" stroke-width="2.5" stroke-linecap="round"/></svg>
  </div>
  <h1 class="abs hero-title">LIFE AND<br>BUSINESS COACH</h1>
</header>

<section class="abs about">
  <div class="photo about-photo" role="img" aria-label="Photo of hands typing on a laptop on a desk"></div>
  <svg class="abs about-arrow" width="110" height="150" viewBox="0 0 110 150"><path d="M70 10 C110 50 100 110 20 130" fill="none" stroke="#aaa" stroke-width="3"/><path d="M36 116 L18 131 L40 138" fill="none" stroke="#aaa" stroke-width="3"/></svg>
  <h2>About Tobias</h2>
  <h4>I'm an online marketer</h4>
  <p class="copy" style="top:382px">Tobias helps founders build calm, steady businesses through clear plans, honest coaching and simple habits that last. Every session focuses on one real step you can take this week.</p>
  <p class="copy" style="top:470px">He has spent twelve years testing marketing ideas online, and he shares what works in plain words so you can grow with less guesswork and more confidence.</p>
  <div class="stats">
    <div class="stat" style="background:var(--red)"><i></i><div><b>19.8K</b><span>Fans</span></div></div>
    <div class="stat" style="background:var(--fb)"><i></i><div><b>118.3K</b><span>Fans</span></div></div>
    <div class="stat" style="background:var(--slate)"><i></i><div><b>80.9K</b><span>Followers</span></div></div>
    <div class="stat" style="background:var(--sky)"><i></i><div><b>80.6K</b><span>Followers</span></div></div>
  </div>
</section>

<!-- newsletter sits over hero and about -->
<div class="abs newsletter">
  <h3>JOIN US AND SIGN UP TO NEWSLETTER</h3>
  <div class="form-row">
    <div class="field">Enter Name</div>
    <div class="field">Enter Address</div>
    <div class="btn-sign">SIGN UP</div>
  </div>
  <p>We never share your information with anyone</p>
</div>

<section class="resources">
  <h2 class="section-title" style="top:1618px">Featured Resources</h2>
  <div class="card-img" style="left:100px;top:1724px;background:linear-gradient(135deg,#e9ecef,#b9c1c9)" role="img" aria-label="Photo of a hand signing a document"></div>
  <div class="card-img" style="left:440px;top:1724px;background:linear-gradient(135deg,#cfc6bc,#8c8178)" role="img" aria-label="Photo of a team working together at a table"></div>
  <div class="card-img" style="left:780px;top:1724px;background:linear-gradient(135deg,#dfe2e6,#5f6670)" role="img" aria-label="Photo of a speaker presenting to an audience"></div>
  <div class="card-title" style="left:100px;top:1980px">Saepe eveniet</div>
  <div class="card-title" style="left:440px;top:1980px">Nam libero</div>
  <div class="card-title" style="left:780px;top:1980px">Cum solutndi</div>
  <p class="card-text" style="left:110px;top:2020px">Short guides and worksheets to plan your week with focus.</p>
  <p class="card-text" style="left:450px;top:2020px">Simple templates that keep client work clear and on time.</p>
  <p class="card-text" style="left:790px;top:2020px">Talks and notes that help you speak with more confidence.</p>
  <div class="btn" style="left:500px;top:2138px;width:200px;height:46px">View More
    <svg width="16" height="12" viewBox="0 0 16 12"><path d="M1 6h13M9 1l5 5-5 5" fill="none" stroke="#fff" stroke-width="2"/></svg></div>
</section>

<section class="abs video">
  <div class="photo video-photo" role="img" aria-label="Photo of a person using a smartphone beside a laptop"></div>
  <svg class="abs play" width="90" height="90" viewBox="0 0 90 90"><circle cx="45" cy="45" r="42" fill="rgba(255,255,255,.15)" stroke="#fff" stroke-width="3"/><path d="M37 30 L60 45 L37 60Z" fill="#fff"/></svg>
  <h3>Nam libero tempore<br>cum soluta nobit eligend</h3>
  <p>Watch how small daily routines turn into steady growth. In this short video Tobias walks through the three questions he asks every new client before planning begins.</p>
  <div class="btn" style="left:614px;top:390px;width:176px;height:46px">Play Video
    <svg width="14" height="14" viewBox="0 0 14 14"><path d="M2 1 L12 7 L2 13Z" fill="#fff"/></svg></div>
</section>

<section class="blog">
  <h2 class="section-title" style="top:3008px">Blog Posts</h2>
  <div class="card-img" style="left:100px;top:3110px;height:210px;background:linear-gradient(135deg,#c8b8a8,#5d5048)" role="img" aria-label="Photo of colleagues discussing at a meeting"></div>
  <div class="card-img" style="left:440px;top:3110px;height:210px;background:linear-gradient(135deg,#8f9aa8,#3d3a3a)" role="img" aria-label="Photo of a business presentation in a conference room"></div>
  <div class="card-img" style="left:780px;top:3110px;height:210px;background:linear-gradient(135deg,#d8d2cc,#4a4440)" role="img" aria-label="Photo of hands typing on a laptop keyboard"></div>
  <div class="post-title" style="left:100px;top:3378px">SED QUIA NON NUMQUAM EIUS</div>
  <div class="post-title" style="left:440px;top:3378px">SED QUIA NON NUMQUAM EIUS</div>
  <div class="post-title" style="left:780px;top:3378px">SED QUIA NON NUMQUAM EIUS</div>
  <p class="post-text" style="left:100px;top:3410px">Notes on pricing, planning and keeping clients happy over time.</p>
  <p class="post-text" style="left:440px;top:3410px">Ideas for writing offers that feel honest and still sell well.</p>
  <p class="post-text" style="left:780px;top:3410px">A calm way to review your month and choose the next goal.</p>
  <div class="btn" style="left:100px;top:3520px;width:108px;height:40px;font-size:13px">Read More</div>
  <div class="btn" style="left:440px;top:3520px;width:108px;height:40px;font-size:13px">Read More</div>
  <div class="btn" style="left:780px;top:3520px;width:108px;height:40px;font-size:13px">Read More</div>
</section>

<section class="abs reach">
  <div class="photo reach-bg" role="img" aria-label="Dark photo of a person working at a laptop"></div>
  <div class="photo reach-map" role="img" aria-label="Dotted world map illustration"></div>
  <h2>Reach Customers Globally</h2>
  <div class="abs avatar" role="img" aria-label="Client portrait"></div>
  <div class="abs avatar-badge"></div>
  <p class="quote">Working with Tobias gave our team a clear direction. Within three months we reached customers in new markets and doubled our monthly sign-ups.</p>
  <div class="quote-name">— <b>Clara Wendt</b></div>
  <div class="abs dots"><span></span><span></span><span></span></div>
</section>

<section class="abs partners">
  <span class="partner">Corvane</span>
  <span class="partner">Lumetra</span>
  <span class="partner">Pinewick</span>
  <span class="partner">Streamly</span>
  <span class="partner">Chirpwell</span>
</section>

<footer class="abs footer">
  <h5 style="left:100px;top:96px">ABOUT ME</h5>
  <p class="about-text">A short note about Tobias, his coaching work and the people he serves. Reach out any time for a friendly first talk about your goals.</p>
  <h5 style="left:590px;top:96px">LET'S CONNECT</h5>
  <div class="abs socials"><span></span><span></span><span></span><span></span><span></span><span></span><span></span></div>
  <div class="abs foot-avatar" role="img" aria-label="Profile portrait placeholder"></div>
  <div class="foot-name">Tobias</div>
  <div class="abs foot-rule"></div>
  <div class="abs foot-nav"><span>HOME</span><span>ABOUT</span><span>BLOG</span><span>VIDEO</span><span>RESOURCES</span><span>CONTACT</span></div>
  <div class="abs foot-legal"><span>PRIVACY POLICY</span><span>TERMS OF USE</span><span>SITEMAP DISCLOSURE</span></div>
  <div class="abs copyright">Copyright © 2018 Tobias Life. All Rights Reserved.</div>
</footer>

</body>
</html>
```